Business Card Design

New business card design

Target Market(s)

Residential & Commercial Property Managers

Industry/Entity Type

Plumbing Services

Contact Information for Business Card

Name - Rowan Keddle, title - Director, Phone Number - 0431 286 517, email - rowan@tbk-plumbing.com.au, Company ABN - 73 215 904 386,

Font styles to use
Sans Serif

Colors
0054AA
0677BA
7BADD7
CADEEF
E8F1F8

```html
<!DOCTYPE html>
<html lang="en">
<head>
<meta charset="utf-8">
<title>TBK Plumbing Services – Business Card</title>
<link href="https://fonts.googleapis.com/css2?family=Poppins:wght@300;400;600&display=swap" rel="stylesheet">
<style>
  :root {
    --stage: #222222;
    --card-front: #6f675b;
    --card-front-ink: #4f4941;
    --card-back: #1c232b;
    --card-back-glow: #242d37;
    --blue: #29a8e0;
    --white: #ffffff;
    --taupe: #8a8175;
  }
  * { margin: 0; padding: 0; box-sizing: border-box; }
  html, body {
    width: 1200px; height: 711px; overflow: hidden;
    background: var(--stage);
    font-family: "Poppins", sans-serif;
  }
  .stage {
    width: 1200px; height: 711px;
    display: flex; align-items: center; justify-content: center; gap: 50px;
  }
  .card {
    width: 540px; height: 310px;
    border-radius: 4px;
    position: relative;
    display: flex; flex-direction: column; align-items: center;
  }
  .card--front {
    background: var(--card-front);
    justify-content: center;
  }
  .card--back {
    background: radial-gradient(ellipse at 50% 45%, var(--card-back-glow), var(--card-back) 70%);
    padding-top: 38px;
  }
  .brand {
    display: flex; align-items: center; gap: 12px;
  }
  .brand__dot {
    width: 18px; height: 18px; border-radius: 50%;
    background: var(--blue);
  }
  .brand__name {
    font-weight: 300;
    font-size: 32px;
    letter-spacing: 2px;
  }
  .card--front .brand__name { color: var(--card-front-ink); font-size: 38px; }
  .card--back .brand__name { color: var(--white); }
  .person {
    margin-top: 30px;
    font-size: 26px; line-height: 1;
  }
  .person__first { color: var(--blue); font-weight: 600; }
  .person__last { color: var(--taupe); font-weight: 300; }
  .role {
    color: var(--white); font-size: 13px; margin-top: 6px;
  }
  .abn {
    color: var(--blue); font-size: 13px; margin-top: 16px; letter-spacing: .5px;
  }
  .icons {
    display: flex; gap: 10px; margin-top: 12px;
  }
  .icons svg { width: 20px; height: 20px; }
  .contact {
    margin-top: 10px; text-align: center;
    color: var(--white); font-size: 12px; line-height: 1.55;
  }
</style>
</head>
<body>
<main class="stage">
  <section class="card card--front" aria-label="Card front">
    <div class="brand">
      <span class="brand__name">TBK Plumbing Services</span>
    </div>
  </section>

  <section class="card card--back" aria-label="Card back">
    <div class="brand">
      <span class="brand__name">TBK Plumbing Services</span>
      <span class="brand__dot"></span>
    </div>
    <p class="person"><span class="person__first">Rowan</span> <span class="person__last">Keddle</span></p>
    <p class="role">Director</p>
    <p class="abn">ABN - 73 215 904 386</p>
    <div class="icons">
      <svg viewBox="0 0 20 20" aria-label="Phone"><rect width="20" height="20" rx="5" fill="#29a8e0"/><path d="M6 5l2 0 1 3-1.5 1a6 6 0 0 0 3.5 3.5L12 11l3 1v2a1 1 0 0 1-1 1A9 9 0 0 1 5 6a1 1 0 0 1 1-1z" fill="#fff"/></svg>
      <svg viewBox="0 0 20 20" aria-label="Email"><rect width="20" height="20" rx="5" fill="#29a8e0"/><rect x="4.5" y="6" width="11" height="8" rx="1" fill="#fff"/><path d="M4.5 6.5l5.5 4 5.5-4" stroke="#29a8e0" stroke-width="1.2" fill="none"/></svg>
      <svg viewBox="0 0 20 20" aria-label="Website"><rect width="20" height="20" rx="5" fill="#29a8e0"/><circle cx="10" cy="10" r="5.5" fill="none" stroke="#fff" stroke-width="1.3"/><ellipse cx="10" cy="10" rx="2.3" ry="5.5" fill="none" stroke="#fff" stroke-width="1.1"/><path d="M4.5 10h11" stroke="#fff" stroke-width="1.1"/></svg>
    </div>
    <div class="contact">
      <p>0431 286 517</p>
      <p>www.tbk-plumbing.com.au</p>
      <p>rowan@tbk-plumbing.com.au</p>
    </div>
  </section>
</main>
</body>
</html>
```